New Business Card Design Project

I need a design for business cards, i am an electrical business called "Corvane Electrical and Communications" i need the cards to be double sided with the company logo on the back (attached) the front needs to say my company name, web site, email address, telephone number, and ABN number and electrical license number. I am open to different arrangements of the information but would like the background to be incorporating something electrical or something that looks smart. open to all additional ideas also.

The company colours are orange and grey see logo attached.

Business Name: Corvane Electrical and Communications
Website: corvaneelectricalandcomms.example.com.au
Email: brent@corvaneelectricalandcomms.example.com.au
Telephone(mobile): 0481209736
ABN: 71208349162
Lic No: 418273D

Target Market(s)

Business entities, Project Managers, Accounts, Clients

Industry/Entity Type

Electrician

Contact Information for Business Card

I need a design for business cards, i am an electrical business called "Corvane Electrical and Communications" i need the cards to be double sided with the company logo on the back (attached) the front needs to say my company name

Font styles to use
Serif
Sans Serif

Colors
f37122
5c5c5c

Requirements
Must have
• Must have the Logo on the back open to different ways of it being on the back but had in mind to keep it central but again open to other options
Nice to have
• A real modern cool background that is eye catching yet contemporary
Should not have
• No backgrounds of a light bulb or plug or anything like that

```html
<!DOCTYPE html>
<html lang="en">
<head>
<meta charset="utf-8">
<title>Corvane Electrical and Communications – Business Card</title>
<link rel="stylesheet" href="https://fonts.googleapis.com/css2?family=Open+Sans:wght@400;600;700&display=swap">
<style>
  :root {
    --backdrop: #4a4341;
    --card: #121212;
    --card-edge: #1c1c1c;
    --orange: #f5a017;
    --white: #f2f2f2;
    --grey: #8a8a8a;
    --rule: #5c5c5c;
  }
  * { margin: 0; padding: 0; box-sizing: border-box; }
  html, body {
    width: 1200px; height: 814px; overflow: hidden;
    background: var(--backdrop);
    font-family: "Open Sans", Arial, sans-serif;
  }
  .canvas {
    width: 1200px; height: 814px;
    display: flex; align-items: center; justify-content: center; gap: 40px;
  }
  .card {
    position: relative;
    width: 540px; height: 330px;
    background: var(--card);
    border: 1px solid var(--card-edge);
    box-shadow: 0 14px 30px rgba(0,0,0,.45);
  }
  /* front */
  .brand {
    position: absolute; top: 40px; right: 36px;
    display: flex; align-items: center; gap: 10px;
  }
  .brand-dot { width: 14px; height: 14px; border-radius: 50%; background: var(--orange); }
  .brand-name {
    color: var(--white); font-weight: 600; font-size: 15px;
    line-height: 1.25; text-align: right; letter-spacing: .04em;
  }
  .brand-rule {
    position: absolute; top: 112px; left: 230px; right: 36px;
    height: 1px; background: var(--rule);
  }
  .registration {
    position: absolute; top: 136px; right: 36px;
    color: var(--white); font-size: 13px; line-height: 1.45; text-align: right;
  }
  .person { position: absolute; left: 36px; top: 196px; right: 36px; }
  .person-name-row { display: flex; align-items: flex-end; gap: 6px; }
  .person-name { color: var(--orange); font-weight: 700; font-size: 17px; letter-spacing: .02em; }
  .person-name-rule { width: 150px; height: 1px; background: var(--rule); margin-bottom: 5px; }
  .person-title { color: var(--white); font-size: 12px; margin-top: 2px; letter-spacing: .03em; }
  .contact-list { list-style: none; margin-top: 12px; }
  .contact-item {
    display: flex; align-items: center; gap: 8px;
    color: var(--white); font-size: 12px; line-height: 20px;
  }
  .contact-icon { width: 12px; height: 12px; flex: none; }
  /* back */
  .back-inner {
    position: absolute; inset: 0;
    display: flex; flex-direction: column; align-items: center; justify-content: center; gap: 22px;
  }
  .back-name {
    color: var(--orange); font-weight: 600; font-size: 20px;
    letter-spacing: .05em; text-align: center; line-height: 1.3;
  }
  .back-web { color: var(--white); font-size: 11px; letter-spacing: .08em; }
</style>
</head>
<body>
<main class="canvas">
  <section class="card card-front" aria-label="Card front">
    <div class="brand">
      <div class="brand-name">CORVANE<br>ELECTRICAL &amp; COMMUNICATIONS</div>
      <span class="brand-dot"></span>
    </div>
    <div class="brand-rule"></div>
    <div class="registration">ABN: 71208349162<br>Lic No: 418273D</div>
    <div class="person">
      <div class="person-name-row">
        <span class="person-name">MARCUS REID</span>
        <span class="person-name-rule"></span>
      </div>
      <div class="person-title">CEO/FOUNDER</div>
      <ul class="contact-list">
        <li class="contact-item">
          <svg class="contact-icon" viewBox="0 0 12 12"><rect x="3" y="0.5" width="6" height="11" rx="1.2" fill="var(--orange)"/><rect x="4" y="2" width="4" height="7" fill="var(--card)"/></svg>
          0481209736
        </li>
        <li class="contact-item">
          <svg class="contact-icon" viewBox="0 0 12 12"><rect x="0.5" y="2.5" width="11" height="7.5" rx="1" fill="var(--orange)"/><path d="M1 3l5 4 5-4" fill="none" stroke="var(--card)" stroke-width="1"/></svg>
          brent@corvaneelectricalandcomms.example.com.au
        </li>
        <li class="contact-item">
          <svg class="contact-icon" viewBox="0 0 12 12"><circle cx="6" cy="6" r="5.5" fill="var(--orange)"/><path d="M0.5 6h11M6 0.5c-2.5 3-2.5 8 0 11M6 0.5c2.5 3 2.5 8 0 11" fill="none" stroke="var(--card)" stroke-width=".8"/></svg>
          corvaneelectricalandcomms.example.com.au
        </li>
      </ul>
    </div>
  </section>

  <section class="card card-back" aria-label="Card back">
    <div class="back-inner">
      <div class="back-name">CORVANE<br>ELECTRICAL &amp; COMMUNICATIONS</div>
      <div class="back-web">www.corvaneelectricalandcomms.example.com.au</div>
    </div>
  </section>
</main>
</body>
</html>
```